Beacon Advisory Website

I currently have a website www.beaconadvisoryinc.com. We are a IT Consulting Company. Our website will pretty much tell out our services. I am looking to enhance my website and make it look more professional. Looking for very classy and Contemporary look and design for my website.

It Company

```html
<!DOCTYPE html>
<html lang="en">
<head>
<meta charset="utf-8">
<title>Beacon Advisory</title>
<link href="https://fonts.googleapis.com/css2?family=Montserrat:wght@400;700;800&family=Roboto:ital,wght@0,300;0,400;0,500;1,400&display=swap" rel="stylesheet">
<style>
:root{
  --blue:#0aa0dc;
  --blue-dark:#0a8bc2;
  --footer-head:#0b5f86;
  --ink:#222;
  --text:#666;
  --line:#dcdcdc;
  --hero:#d5d5d5;
  --page:#e6e6e6;
  --white:#fff;
  --quote:#eef6fa;
}
*{margin:0;padding:0;box-sizing:border-box}
html,body{width:1200px;height:2941px;overflow:hidden}
body{position:relative;background:var(--white);font-family:"Roboto",Arial,sans-serif;color:var(--text)}
.abs{position:absolute}
.topstrip{left:0;top:0;width:1200px;height:16px;background:var(--page)}
.header{left:0;top:16px;width:1200px;height:82px;background:var(--white)}
.logo{left:80px;top:22px;display:flex;align-items:center;gap:10px}
.logo-mark{width:38px;height:38px;background:var(--blue)}
.logo-name{font-family:"Montserrat",Arial,sans-serif;font-weight:700;font-size:17px;color:var(--blue);line-height:1}
.nav{left:326px;top:0;height:82px;display:flex;gap:30px;font-family:"Montserrat",Arial,sans-serif;font-size:14px;color:#333}
.nav a{display:flex;align-items:center;height:82px;color:#333;text-decoration:none;position:relative}
.nav a.active::after{content:"";position:absolute;left:0;right:0;bottom:0;height:3px;background:#333}
.search{left:1040px;top:0;width:84px;height:82px;background:var(--blue);display:flex;align-items:center;justify-content:center}
.hero{left:0;top:98px;width:1200px;height:559px;background:var(--hero);overflow:hidden}
.hero-title{left:78px;top:150px;font-family:"Montserrat",Arial,sans-serif;font-weight:800;font-size:80px;line-height:76px;color:#7f8ea8;letter-spacing:2px}
.hero-scene{left:372px;top:108px;width:828px;height:451px;background:linear-gradient(160deg,#cfcfcf 0%,#bfc4c9 45%,#b08d63 62%,#d9d9d9 80%)}
.services{left:0;top:657px;width:1200px;height:343px}
.service{position:absolute;top:0;width:357px;text-align:center}
.service .icon{margin:52px auto 0;width:102px;height:102px;border-radius:50%;border:2px solid var(--blue);display:flex;align-items:center;justify-content:center}
.service .icon.solid{background:#666;border-color:#666}
.service h3{margin-top:24px;font-weight:400;font-size:21px;color:var(--blue)}
.service h3.dark{color:var(--ink)}
.service p{margin:14px auto 0;width:300px;font-size:13.5px;line-height:23px;color:var(--text)}
.divider{top:745px;width:1px;height:215px;background:var(--line)}
.stats{left:0;top:1000px;width:1200px;height:210px;background:var(--blue);color:var(--white)}
.stat{position:absolute;top:40px;width:240px;text-align:center}
.stat .num{margin-top:14px;font-size:28px;line-height:32px}
.stat .label{margin-top:4px;font-size:14px;letter-spacing:.3px}
.tablet{left:78px;top:1239px;width:510px;height:407px;border-radius:30px;background:linear-gradient(150deg,#f2f2f2,#d8d8d8 60%,#bdbdbd)}
.h2{font-weight:300;font-size:40px;color:var(--ink);line-height:48px}
.h2 em{font-style:normal;color:var(--blue)}
.h2 .under{position:relative}
.h2 .under::after{content:"";position:absolute;left:0;right:0;bottom:-6px;height:2px;background:var(--ink)}
.about-title{left:623px;top:1258px}
.about-text{left:623px;top:1340px;width:495px;font-size:14px;line-height:23px;color:var(--text)}
.btn{left:621px;top:1584px;width:147px;height:53px;border:2px solid var(--blue);color:var(--blue);font-size:15px;display:flex;align-items:center;justify-content:center}
.portfolio-bar{left:0;top:1700px;width:1200px;height:84px;background:var(--blue);color:var(--white)}
.portfolio-bar h2{position:absolute;left:82px;top:18px;font-weight:300;font-size:38px}
.filter{position:absolute;top:34px;font-size:14px}
.tile{position:absolute}
.tile.hover{background:rgba(10,160,220,.85);display:flex;align-items:center;justify-content:center}
.clients-say{left:78px;top:2240px}
.quote{left:78px;top:2326px;width:499px;height:202px;background:var(--quote);border-bottom:2px solid var(--blue);padding:30px 32px;font-size:13.5px;line-height:23px;color:#555}
.avatar{left:108px;top:2544px;width:53px;height:51px;background:linear-gradient(#c9b8a6,#8a7b6d)}
.author{left:174px;top:2557px;font-size:18px;color:#333;letter-spacing:.5px}
.arrows{left:520px;top:2557px;display:flex;gap:14px}
.our-clients{left:626px;top:2240px}
.client{position:absolute;display:flex;align-items:center;justify-content:center;gap:8px;font-size:15px;color:#7a7a7a}
.client .dot{width:18px;height:18px;border-radius:50%;background:#9a9a9a}
.client.featured{background:var(--blue);color:var(--white)}
.client.featured .dot{background:var(--white)}
.footer{left:0;top:2646px;width:1200px;height:231px;background:var(--blue);color:var(--white)}
.fcol{position:absolute;top:26px}
.fcol h4{font-weight:400;font-size:17px;color:var(--footer-head);margin-bottom:20px}
.contact-row{display:flex;gap:16px;align-items:flex-start;font-size:13.5px;line-height:20px;margin-bottom:18px}
.post{display:flex;gap:12px;margin-bottom:14px;font-size:13.5px;line-height:20px}
.post .thumb{width:52px;height:52px;border-radius:50%;background:linear-gradient(#b59a80,#6f5c4d);flex:none}
.post .date{color:#0b7fb1;font-size:12.5px}
.news p{font-size:13.5px;line-height:22px;width:320px}
.news-field{margin-top:16px;width:312px;height:54px;background:var(--white);display:flex}
.news-field span{flex:1;padding:16px 22px;font-style:italic;color:var(--blue);font-size:14px}
.news-field i{width:54px;background:var(--blue);border:2px solid var(--white);display:flex;align-items:center;justify-content:center}
.bottombar{left:0;top:2877px;width:1200px;height:64px;background:var(--blue-dark);color:var(--white);font-size:13.5px}
.bottombar .copy{position:absolute;left:80px;top:24px}
.bottombar .copy b{font-weight:400;color:#7fd3f3}
.social{position:absolute;right:80px;top:25px;display:flex;gap:22px}
.social span{width:14px;height:14px;border-radius:50%;background:#5cc3ec}
</style>
</head>
<body>
<div class="abs topstrip"></div>

<header class="abs header">
  <div class="abs logo"><div class="logo-mark"></div><div class="logo-name">Beacon Advisory</div></div>
  <nav class="abs nav">
    <a class="active">HOME</a><a>COMPANY</a><a>SERVICES</a><a>SOLUTIONS</a><a>RESOURCES</a><a>CAREER</a><a>CONTACT</a>
  </nav>
  <div class="abs search">
    <svg width="18" height="18" viewBox="0 0 18 18"><circle cx="7.5" cy="7.5" r="5.5" fill="none" stroke="#fff" stroke-width="2.4"/><line x1="11.5" y1="11.5" x2="16" y2="16" stroke="#fff" stroke-width="2.6"/></svg>
  </div>
</header>

<section class="abs hero">
  <div class="abs hero-scene" role="img" aria-label="Workspace with desk, computer monitor, stool and framed picture"></div>
  <h1 class="abs hero-title">STRONG<br>SOLUTION</h1>
</section>

<section class="abs services">
  <div class="service" style="left:64px">
    <div class="icon"><svg width="44" height="44" viewBox="0 0 44 44" fill="none" stroke="#0aa0dc" stroke-width="2"><path d="M15 20a7 7 0 1 1 14 0c0 3-3 5-3 8h-8c0-3-3-5-3-8z"/><line x1="18" y1="32" x2="26" y2="32"/><line x1="19" y1="35" x2="25" y2="35"/><line x1="22" y1="5" x2="22" y2="9"/><line x1="9" y1="20" x2="5" y2="20"/><line x1="35" y1="20" x2="39" y2="20"/><line x1="12" y1="10" x2="9" y2="7"/><line x1="32" y1="10" x2="35" y2="7"/></svg></div>
    <h3>Consulting</h3>
    <p>Beacon Advisory has certified professional consultants to work with you to help increase the business by providing IT services...</p>
  </div>
  <div class="service" style="left:421px">
    <div class="icon solid"><svg width="44" height="44" viewBox="0 0 44 44" fill="none" stroke="#fff" stroke-width="2"><circle cx="19" cy="14" r="7"/><path d="M6 36c0-8 6-12 13-12 3 0 5 .5 7 2"/><circle cx="30" cy="31" r="6"/><path d="M27 31l2 2 4-4"/></svg></div>
    <h3 class="dark">Staff Augmentation</h3>
    <p>For years Beacon Advisory has been offering our customers the ability to augment their existing staff with temporary highly skilled IT professionals...</p>
  </div>
  <div class="service" style="left:778px">
    <div class="icon"><svg width="44" height="44" viewBox="0 0 44 44" fill="none" stroke="#0aa0dc" stroke-width="2"><circle cx="22" cy="22" r="14"/><circle cx="22" cy="22" r="8"/><circle cx="22" cy="22" r="3"/><line x1="22" y1="4" x2="22" y2="10"/><line x1="22" y1="34" x2="22" y2="40"/><line x1="4" y1="22" x2="10" y2="22"/><line x1="34" y1="22" x2="40" y2="22"/></svg></div>
    <h3>Offshore</h3>
    <p>Our Offshore development model has a unique distinction of providing efficient software solutions with cost and quality advantage...</p>
  </div>
</section>
<div class="abs divider" style="left:421px"></div>
<div class="abs divider" style="left:778px"></div>

<section class="abs stats">
  <div class="stat" style="left:84px">
    <svg width="60" height="60" viewBox="0 0 60 60" fill="none" stroke="#fff" stroke-width="2"><circle cx="30" cy="22" r="9"/><circle cx="30" cy="22" r="14" stroke-dasharray="5 4"/><path d="M8 38l12 12h20l12-12"/></svg>
    <div class="num">2,500</div><div class="label">PROJECT COMPLETED</div>
  </div>
  <div class="stat" style="left:347px">
    <svg width="60" height="60" viewBox="0 0 60 60" fill="none" stroke="#fff" stroke-width="2"><path d="M6 26l12-12 10 6 6-4 20 12-12 12-10-6-8 8-12-10z"/><path d="M22 34l6 6M28 30l6 6M34 28l6 6"/></svg>
    <div class="num">400</div><div class="label">HAPPY CLIENTS</div>
  </div>
  <div class="stat" style="left:611px">
    <svg width="60" height="60" viewBox="0 0 60 60" fill="none" stroke="#fff" stroke-width="2"><circle cx="30" cy="16" r="7"/><circle cx="14" cy="24" r="5"/><circle cx="46" cy="24" r="5"/><path d="M18 50c0-12 6-18 12-18s12 6 12 18"/><path d="M4 48c0-8 4-13 10-13 3 0 5 1 6 3"/><path d="M56 48c0-8-4-13-10-13-3 0-5 1-6 3"/></svg>
    <div class="num">100</div><div class="label">TEAM MEMBERS</div>
  </div>
  <div class="stat" style="left:876px">
    <svg width="60" height="60" viewBox="0 0 60 60" fill="none" stroke="#fff" stroke-width="2"><circle cx="30" cy="22" r="15"/><circle cx="30" cy="22" r="9"/><path d="M20 34l-6 20 8-4 5 7 3-14"/><path d="M40 34l6 20-8-4-5 7-3-14"/></svg>
    <div class="num">20</div><div class="label">AWARDS WON</div>
  </div>
</section>

<div class="abs tablet" role="img" aria-label="Tablet showing a blog page layout"></div>
<h2 class="abs h2 about-title"><span class="under">About</span> <em>BEACON</em></h2>
<p class="abs about-text">Lorem Ipsum is simply dummy text of the printing and typesetting industry. Lorem Ipsum has been the industry's standard dummy text ever since the 1500s, when an unknown printer took a galley of type and scrambled it to make a type specimen book. It has survived not only five centuries, but also the leap into electronic typesetting, remaining essentially unchanged. It was popularised in the 1960s with the release of transfer sheets containing Lorem Ipsum passages, and more recently with desktop publishing software including versions of Lorem Ipsum.</p>
<div class="abs btn">LOAD MORE</div>

<section class="abs portfolio-bar">
  <h2>Our PORTFOLIO</h2>
  <span class="filter" style="left:614px">All</span>
  <span class="filter" style="left:678px">Dashboards</span>
  <span class="filter" style="left:804px">Data warehousing</span>
  <span class="filter" style="left:967px">BPM</span>
</section>
<div class="abs" style="left:0;top:1784px;width:1200px;height:398px">
  <div class="tile" style="left:0;top:0;width:200px;height:398px;background:linear-gradient(#d8d4cf,#8c8782)" role="img" aria-label="Businessman on the phone holding a tablet"></div>
  <div class="tile" style="left:200px;top:0;width:400px;height:199px;background:linear-gradient(#5a4d44,#d9cfc3)" role="img" aria-label="Hands holding a consulting sign"></div>
  <div class="tile" style="left:600px;top:0;width:200px;height:199px;background:linear-gradient(#e2e2e2,#8a8f96)" role="img" aria-label="Business team meeting"></div>
  <div class="tile" style="left:800px;top:0;width:200px;height:199px;background:linear-gradient(#d6d6d6,#6e737a)" role="img" aria-label="Businessman thinking at a laptop"></div>
  <div class="tile" style="left:1000px;top:0;width:200px;height:199px;background:linear-gradient(#f0f0f0,#4e4a48)" role="img" aria-label="Businesswomen reviewing documents"></div>
  <div class="tile hover" style="left:200px;top:199px;width:200px;height:199px" role="img" aria-label="Project photo with view overlay">
    <svg width="26" height="26" viewBox="0 0 18 18"><circle cx="7.5" cy="7.5" r="5.5" fill="none" stroke="#fff" stroke-width="2"/><line x1="11.5" y1="11.5" x2="16" y2="16" stroke="#fff" stroke-width="2.2"/></svg>
  </div>
  <div class="tile" style="left:400px;top:199px;width:200px;height:199px;background:linear-gradient(#bfc4ca,#3c3f44)" role="img" aria-label="Colleagues working on a laptop"></div>
  <div class="tile" style="left:600px;top:199px;width:400px;height:199px;background:linear-gradient(#eef2f5,#9aa3ab)" role="img" aria-label="Business people walking in an office"></div>
  <div class="tile" style="left:1000px;top:199px;width:200px;height:199px;background:linear-gradient(#f4f1ec,#b59577)" role="img" aria-label="Smiling woman writing notes"></div>
</div>

<h2 class="abs h2 clients-say"><span class="under">What</span> <em>CLIENTS</em> Say</h2>
<div class="abs quote">"Lorem Ipsum is simply dummy text of the printing and typesetting industry. Lorem Ipsum has been the industry's standard dummy text ever since the 1500s, when an unknown printer took a galley of type and scrambled it to make a type specimen book. It has survived not only five centuries, but also the leap into electronic typesetting, remaining essentially unchanged."</div>
<div class="abs avatar" role="img" aria-label="Client portrait"></div>
<div class="abs author">JOHN DOE</div>
<div class="abs arrows">
  <svg width="12" height="18" viewBox="0 0 12 18"><path d="M10 2L3 9l7 7" fill="none" stroke="#0aa0dc" stroke-width="2"/></svg>
  <svg width="12" height="18" viewBox="0 0 12 18"><path d="M2 2l7 7-7 7" fill="none" stroke="#333" stroke-width="2"/></svg>
</div>

<h2 class="abs h2 our-clients"><span class="under">Our</span> <em>CLIENTS</em></h2>
<div class="abs" style="left:620px;top:2352px;width:520px;height:230px">
  <div class="client" style="left:0;top:0;width:160px;height:74px"><span class="dot"></span>Orvane Cam</div>
  <div class="client" style="left:180px;top:0;width:160px;height:74px"><span class="dot"></span>Partline Group</div>
  <div class="client" style="left:356px;top:0;width:160px;height:74px"><span class="dot"></span>Halden Secure</div>
  <div class="client" style="left:24px;top:124px;width:120px;height:74px"><span class="dot"></span>Vantora</div>
  <div class="client featured" style="left:170px;top:99px;width:167px;height:124px"><span class="dot"></span>Cloudmere</div>
  <div class="client" style="left:346px;top:124px;width:160px;height:74px"><span class="dot"></span>Tessaline</div>
</div>

<footer class="abs footer">
  <div class="fcol" style="left:80px">
    <h4>Contact Info</h4>
    <div class="contact-row"><svg width="20" height="22" viewBox="0 0 20 22" fill="none" stroke="#fff" stroke-width="1.6"><path d="M10 21s7-7 7-12a7 7 0 0 0-14 0c0 5 7 12 7 12z"/><circle cx="10" cy="9" r="2.5"/></svg><span>418 Linden Row, Suite 12<br>Fairhaven, NJ 07190</span></div>
    <div class="contact-row"><svg width="20" height="20" viewBox="0 0 20 20" fill="none" stroke="#fff" stroke-width="1.6"><path d="M4 2l4 1 1 4-2 2a11 11 0 0 0 4 4l2-2 4 1 1 4c-8 1-15-6-14-14z"/></svg><span>+1 (555) 014 2290</span></div>
    <div class="contact-row"><svg width="20" height="16" viewBox="0 0 20 16" fill="none" stroke="#fff" stroke-width="1.6"><rect x="1" y="1" width="18" height="14"/><path d="M1 2l9 7 9-7"/></svg><span>info@beaconadvisory.com</span></div>
  </div>
  <div class="fcol" style="left:435px">
    <h4>Blog</h4>
    <div class="post"><div class="thumb" role="img" aria-label="Blog post thumbnail"></div><div>Lorem Ipsum is simply dummy text of the<br>printing and typesetting industry.<br><span class="date">November 30, 2016</span></div></div>
    <div class="post"><div class="thumb" role="img" aria-label="Blog post thumbnail"></div><div>Lorem Ipsum is simply dummy text of the<br>printing and typesetting industry.<br><span class="date">December 5, 2016</span></div></div>
  </div>
  <div class="fcol news" style="left:812px">
    <h4>Newsletter</h4>
    <p>Sign up to get updates about innovative and extra utility new property developed by us.</p>
    <div class="news-field"><span>Type Here...</span><i><svg width="22" height="16" viewBox="0 0 20 16" fill="none" stroke="#fff" stroke-width="1.6"><rect x="1" y="1" width="18" height="14"/><path d="M1 2l9 7 9-7"/></svg></i></div>
  </div>
</footer>

<div class="abs bottombar">
  <div class="copy">© <b>Beacon Advisory</b> 2016. All Rights Reserved</div>
  <div class="social"><span></span><span></span><span></span><span></span></div>
</div>
</body>
</html>
```